Harborview Estates Business Card for Apartment Buildings

Create business cards for resident managers who run apartment buildings. The audience is the public who are searching for apartment rentals, and current residents who live at the apartment building. Key design element will be incorporating the company logo, however, the logo cannot dominate. The building name and manager name are more important than the logo. Current business card design leaves little room for copy, so we may need to reduce the size on the current card to allow for more space for copy.

Target Market(s)

Adults 18-65 years of age, who are looking for an apartment rental, plus current residents who live at our apartment buildings.

Industry/Entity Type

Property Management

Contact Information for Business Card

A major design element will be use of the company logo. Important property and manager contact information must be part of the design. The size of the logo will need to be reduced to make room for building and manager contact copy.

Font styles to use
Sans Serif

Colors
3176b5
000000
959595
ffffff

Requirements
Must have
• 1) Incorporate the company logo.
• 2) Use the company colors (dark blue, black/grey, over white).
• 3) FEATURE THE BUILDING NAME
• 4) FEATURE THE MANAGER NAME
• 5) The company name is less important than BUILDING and MANAGER
• 6) Manager contact information
• **SEE ATTACHED CREATIVE BRIEF**
Nice to have
• 1) Back of card logo watermark
• 2) Ability to write notes on back of carfd
Should not have
• Avoid letting the company logo dominate the card, the building name and manager are more important than the company logo.

```html
<!DOCTYPE html>
<html lang="en">
<head>
<meta charset="utf-8">
<title>Harborview Estates Business Card</title>
<link href="https://fonts.googleapis.com/css2?family=Roboto:wght@400;500;700&family=Roboto+Condensed:wght@700&display=swap" rel="stylesheet">
<style>
  :root {
    --brand-blue: #1769a6;
    --ink-grey: #444446;
    --soft-grey: #959595;
    --card-white: #f4f4f4;
    --backdrop: #2a2a2a;
    --band-dark: #464648;
    --white: #ffffff;
  }
  * { margin: 0; padding: 0; box-sizing: border-box; }
  html, body {
    width: 1200px; height: 960px; overflow: hidden;
    background: var(--backdrop);
    font-family: "Roboto", Arial, sans-serif;
  }
  .card {
    position: absolute;
    width: 600px; height: 343px;
    background: var(--card-white);
    overflow: hidden;
  }
  .card--front { left: 314px; top: 113px; }
  .card--back { left: 311px; top: 472px; }

  .wordmark {
    position: absolute;
    display: flex; align-items: center; gap: 10px;
  }
  .wordmark__square {
    width: 30px; height: 30px; background: var(--brand-blue); flex: none;
  }
  .wordmark__name {
    font-family: "Roboto Condensed", Arial, sans-serif;
    font-weight: 700; font-size: 23px; line-height: 1.05;
    color: var(--brand-blue); letter-spacing: 0.5px;
    text-transform: uppercase;
  }
  .wordmark__name span { display: block; }
  .card--front .wordmark { left: 62px; top: 114px; }

  .divider {
    position: absolute; left: 303px; top: 57px;
    width: 1px; height: 156px; background: #c9c9c9;
  }
  .manager { position: absolute; left: 328px; top: 59px; }
  .manager__name {
    font-family: "Roboto Condensed", Arial, sans-serif;
    font-weight: 700; font-size: 24px; color: var(--brand-blue);
  }
  .manager__title {
    font-size: 15px; font-weight: 500; color: var(--ink-grey); margin-top: 0;
  }
  .contact-list { list-style: none; margin-top: 11px; }
  .contact-list li {
    display: flex; align-items: center; gap: 9px;
    font-size: 14px; color: var(--ink-grey); height: 19px;
  }
  .contact-list svg { width: 13px; height: 13px; fill: var(--brand-blue); flex: none; }

  .building-band {
    position: absolute; left: 0; top: 257px; width: 600px; height: 61px;
    background: var(--brand-blue);
  }
  .building-band__end {
    position: absolute; right: 0; top: 0; width: 150px; height: 61px;
    background: var(--band-dark);
    clip-path: polygon(22% 0, 100% 0, 100% 100%, 22% 100%, 10% 50%);
  }
  .building-band__text {
    position: absolute; left: 0; width: 450px; top: 8px;
    text-align: center; color: var(--white);
  }
  .building-band__name { font-size: 21px; font-weight: 500; }
  .building-band__address { font-size: 14px; margin-top: 1px; }

  .card--back .wordmark { right: 35px; top: 223px; }
  .tagline {
    position: absolute; right: 35px; top: 290px;
    font-size: 14px; font-weight: 700; color: var(--ink-grey);
  }
</style>
</head>
<body>
  <section class="card card--front">
    <div class="wordmark">
      <span class="wordmark__square"></span>
      <span class="wordmark__name"><span>Harborview</span><span>Estates</span></span>
    </div>
    <div class="divider"></div>
    <div class="manager">
      <h1 class="manager__name">Marisol Delgado</h1>
      <p class="manager__title">Resident Manager</p>
      <ul class="contact-list">
        <li><svg viewBox="0 0 16 16"><path d="M3 1l3 3-1.5 2a9 9 0 0 0 5.5 5.5L12 10l3 3-2 2C7 15 1 9 1 3z"/></svg>555-201-4830</li>
        <li><svg viewBox="0 0 16 16"><path d="M4 0h8v16H4zM5.5 2v10h5V2z"/></svg>555-318-7642</li>
        <li><svg viewBox="0 0 16 16"><path d="M4 1h8v4H4zM1 6h14v6h-3v3H4v-3H1zM5 10v4h6v-4z"/></svg>555-402-9150</li>
        <li><svg viewBox="0 0 16 16"><path d="M1 3h14v10H1zM2 4.5v.5l6 4 6-4v-.5z"/></svg>marisol@harborviewest.com</li>
        <li><svg viewBox="0 0 16 16"><circle cx="8" cy="8" r="7"/></svg>www.harborviewest.com</li>
      </ul>
    </div>
    <div class="building-band">
      <div class="building-band__end"></div>
      <div class="building-band__text">
        <h2 class="building-band__name">Linden Court Apartments</h2>
        <p class="building-band__address">2415 Willow Street, Bayside, CA 92000</p>
      </div>
    </div>
  </section>

  <section class="card card--back">
    <div class="wordmark">
      <span class="wordmark__square"></span>
      <span class="wordmark__name"><span>Harborview</span><span>Estates</span></span>
    </div>
    <p class="tagline">Multifamily Property Management</p>
  </section>
</body>
</html>
```